Local Roofing Company Billboard Design

We need a billboard design for an 8' x 32' billboard. This billboard would need to be easily readable and stand out well.
I have uploaded a design that we like - simple, readable, and gets the point across. We do NOT want the $1000 off offer included.
We are looking for a black background with white copy so it will stand out. We want the following on the billboard:
Brindlewick Roofing logo
brindlewick-roofing.example (optional)
555.214.7730 (mandatory)
Photo is optional, depends on how it all lays out
Production file must comply with layout requirements (uploaded).
Target Market(s)
Homeowners
Font styles to use
Other font styles liked:
- match font from logo
Colors
Designer to choose colors to be used in the design.
Requirements
Must have
- Black background, white copy, logo must be large and legible. Colors used must match our logo colors.

```html
<!DOCTYPE html>
<html lang="en">
<head>
<meta charset="UTF-8">
<title>Brindlewick Roofing Billboard</title>
<link href="https://fonts.googleapis.com/css2?family=Arvo:wght@700&family=Montserrat:wght@700&display=swap" rel="stylesheet">
<style>
  :root {
    --board-black: #1f1e1e;
    --brand-orange: #f1531c;
    --copy-white: #ffffff;
    --sky-light: #e4eef6;
    --sky-mid: #b9c4cf;
    --roof-grey: #4a4d52;
    --page-bg: #f2f2f2;
  }
  html, body {
    margin: 0;
    padding: 0;
    width: 1200px;
    height: 857px;
    overflow: hidden;
    background: var(--page-bg);
  }
  .billboard {
    position: absolute;
    left: 20px;
    top: 153px;
    width: 1160px;
    height: 550px;
    background: var(--board-black);
    overflow: hidden;
  }
  .billboard-shapes {
    position: absolute;
    inset: 0;
  }
  .brand-lockup {
    position: absolute;
    left: 60px;
    top: 176px;
    display: flex;
    align-items: center;
    gap: 16px;
  }
  .brand-mark {
    width: 40px;
    height: 40px;
    background: var(--brand-orange);
    flex: none;
  }
  .brand-name {
    margin: 0;
    font-family: "Arvo", Georgia, serif;
    font-weight: 700;
    font-size: 40px;
    line-height: 1;
    color: var(--copy-white);
    white-space: nowrap;
  }
  .phone-line {
    position: absolute;
    left: 60px;
    top: 322px;
    display: flex;
    align-items: center;
    gap: 20px;
  }
  .phone-icon {
    width: 56px;
    height: 56px;
    flex: none;
  }
  .phone-number {
    font-family: "Montserrat", Arial, sans-serif;
    font-weight: 700;
    font-size: 60px;
    line-height: 1;
    color: var(--copy-white);
    letter-spacing: 1px;
    white-space: nowrap;
  }
  .web-address {
    position: absolute;
    left: 60px;
    top: 488px;
    font-family: "Montserrat", Arial, sans-serif;
    font-weight: 700;
    font-size: 28px;
    line-height: 1;
    color: var(--copy-white);
    letter-spacing: 0.5px;
    white-space: nowrap;
  }
</style>
</head>
<body>
  <div class="billboard">
    <svg class="billboard-shapes" width="1160" height="550" viewBox="0 0 1160 550">
      <defs>
        <linearGradient id="houseTones" x1="0" y1="0" x2="0" y2="1">
          <stop offset="0" stop-color="var(--sky-light)"/>
          <stop offset="0.45" stop-color="var(--sky-mid)"/>
          <stop offset="1" stop-color="var(--roof-grey)"/>
        </linearGradient>
      </defs>
      <path role="img" aria-label="Photo of a house with a dark tiled roof, dormer window and chimney under a light sky"
            d="M775 0 H1160 V550 H900 L660 310 Q640 275 660 240 Z"
            fill="url(#houseTones)"/>
      <path class="chevron-band"
            d="M735 0 H785 L668 240 Q650 275 668 310 L912 550 H868 L628 310 Q608 275 628 240 Z"
            fill="var(--brand-orange)"/>
      <path class="chevron-edge"
            d="M720 0 L610 240 Q592 275 610 310 L850 550"
            fill="none" stroke="var(--copy-white)" stroke-width="3"/>
      <path class="web-band"
            d="M0 455 H620 Q670 455 700 500 L735 550 H0 Z"
            fill="var(--brand-orange)"/>
    </svg>

    <div class="brand-lockup">
      <span class="brand-mark" aria-hidden="true"></span>
      <h1 class="brand-name">Brindlewick Roofing</h1>
    </div>

    <div class="phone-line">
      <svg class="phone-icon" viewBox="0 0 74 74" aria-hidden="true">
        <circle cx="37" cy="37" r="37" fill="var(--brand-orange)"/>
        <path d="M27 18 l8 10 -5 5 c3 6 7 10 13 13 l5-5 10 8 -5 7 c-18 -1 -32 -15 -33 -33 z"
              fill="none" stroke="var(--board-black)" stroke-width="4" stroke-linejoin="round"/>
      </svg>
      <span class="phone-number">555.214.7730</span>
    </div>

    <div class="web-address">BRINDLEWICK-ROOFING.EXAMPLE</div>
  </div>
</body>
</html>
```